Design a homepage graphic to show a system journey

We have a software package for parents to update student information and manage school excursions we have attached a concept we like but are open to other ideas so long as they fit the following criteria.
1 It needs to be landscape across the page
2. They are showing a series of processes, each step has its own colour, see below
2.1 The first process is a parent updating their own and students information and approving excursions
2.2 The school then creates and manages the excursion this includes a compliance component
2.3 The school conducts the activity it should show some activity type pictures
2.4 Students return safely to school
3 There can be text boxes within the image to clarify functionality
4. The picture should make anyone watching it understand there is a series of
linked processes the system provides i.e. a journey
There should be the ability to click on each component to link to a specific part of the pager lower down, e.g if the person wanted to look at the school part by clicking on the school it would take them to more information, that information already exists so is not required.
Please review the attached concept diagram and use this a potential guide.
Schools
1 page

```html
<!DOCTYPE html>
<html lang="en">
<head>
<meta charset="utf-8">
<title>School Excursion Journey</title>
<link href="https://fonts.googleapis.com/css2?family=Oswald:wght@500&display=swap" rel="stylesheet">
<style>
  :root {
    --bg: #fdf5ec;
    --road: #f7cb77;
    --road-edge: #7a5028;
    --ink: #6b4620;
    --parent: #ef4f6e;
    --student: #3f898d;
    --approve: #656667;
    --accept: #cf6e3c;
    --manage: #aaa87d;
    --take: #5d7190;
    --conduct: #8fa170;
    --return: #6b9b35;
  }
  * { margin: 0; padding: 0; box-sizing: border-box; }
  html, body { width: 1200px; height: 720px; overflow: hidden; background: var(--bg); }
  .journey { display: block; width: 1200px; height: 720px; }
  .road-edge { fill: none; stroke: var(--road-edge); stroke-width: 254; }
  .road-fill { fill: none; stroke: var(--road); stroke-width: 248; }
  .road-centre { fill: none; stroke: var(--road-edge); stroke-width: 3; stroke-dasharray: 16 10; }
  .label-mask { fill: var(--road); }
  .step-label {
    font-family: 'Oswald', sans-serif; font-weight: 500; font-size: 40px;
    fill: var(--ink); text-anchor: middle; letter-spacing: 0.5px;
  }
  .pin-disc { fill: #fff; stroke-width: 10; }
  .step-link { cursor: pointer; }
  .step-link:hover .pin-disc { fill: #fffaf2; }
</style>
</head>
<body>
<svg class="journey" viewBox="0 0 2474 1484" xmlns="http://www.w3.org/2000/svg">
  <defs>
    <linearGradient id="tree-tone" x1="0" y1="0" x2="0" y2="1">
      <stop offset="0" stop-color="#a9cf4a"/>
      <stop offset="0.7" stop-color="#8cb83a"/>
      <stop offset="1" stop-color="#9a7a4a"/>
    </linearGradient>
    <linearGradient id="bus-tone" x1="0" y1="0" x2="0" y2="1">
      <stop offset="0" stop-color="#f9cf3a"/>
      <stop offset="1" stop-color="#f2b91a"/>
    </linearGradient>
    <linearGradient id="city-tone" x1="0" y1="0" x2="1" y2="0">
      <stop offset="0" stop-color="#f6a23a"/>
      <stop offset="0.5" stop-color="#dfe3ea"/>
      <stop offset="1" stop-color="#f07a6e"/>
    </linearGradient>
    <linearGradient id="rider-tone" x1="0" y1="0" x2="0" y2="1">
      <stop offset="0" stop-color="#f0a050"/>
      <stop offset="1" stop-color="#7fb2de"/>
    </linearGradient>
    <radialGradient id="icon-parent"><stop offset="0" stop-color="#f6b8a6"/><stop offset="1" stop-color="#e66a78"/></radialGradient>
    <radialGradient id="icon-student"><stop offset="0" stop-color="#bfe0f2"/><stop offset="1" stop-color="#6fb1d8"/></radialGradient>
    <radialGradient id="icon-approve"><stop offset="0" stop-color="#fbd36a"/><stop offset="1" stop-color="#ef9a3a"/></radialGradient>
    <radialGradient id="icon-accept"><stop offset="0" stop-color="#c9ecf3"/><stop offset="1" stop-color="#6cc3a8"/></radialGradient>
    <radialGradient id="icon-manage"><stop offset="0" stop-color="#f4b088"/><stop offset="1" stop-color="#e2524a"/></radialGradient>
    <radialGradient id="icon-take"><stop offset="0" stop-color="#b8d8ee"/><stop offset="1" stop-color="#3f8cc4"/></radialGradient>
    <radialGradient id="icon-conduct"><stop offset="0" stop-color="#f9d27a"/><stop offset="1" stop-color="#e35b6a"/></radialGradient>
    <radialGradient id="icon-return"><stop offset="0" stop-color="#fbd7a6"/><stop offset="1" stop-color="#ef8a6a"/></radialGradient>
  </defs>

  <g class="scenery">
    <rect role="img" aria-label="City buildings illustration" x="432" y="272" width="158" height="180" rx="6" fill="url(#city-tone)"/>
    <rect role="img" aria-label="City buildings illustration" x="2228" y="1042" width="160" height="180" rx="6" fill="url(#city-tone)"/>
    <rect role="img" aria-label="Tall tree illustration" x="1194" y="155" width="80" height="200" rx="40" fill="url(#tree-tone)"/>
    <rect role="img" aria-label="Tree illustration" x="2010" y="528" width="138" height="186" rx="50" fill="url(#tree-tone)"/>
    <rect role="img" aria-label="Tree illustration" x="126" y="1100" width="130" height="160" rx="48" fill="url(#tree-tone)"/>
    <rect role="img" aria-label="Tree illustration" x="1518" y="1180" width="128" height="180" rx="48" fill="url(#tree-tone)"/>
    <rect role="img" aria-label="School bus illustration" x="1890" y="304" width="216" height="102" rx="16" fill="url(#bus-tone)"/>
    <rect role="img" aria-label="School bus illustration" x="818" y="1220" width="214" height="102" rx="16" fill="url(#bus-tone)"/>
    <rect role="img" aria-label="Cyclist illustration" x="54" y="718" width="146" height="110" rx="40" fill="url(#rider-tone)" opacity="0.5"/>
    <rect role="img" aria-label="Cyclist illustration" x="2245" y="718" width="146" height="110" rx="40" fill="url(#rider-tone)" opacity="0.5"/>
  </g>

  <g class="road">
    <path class="road-edge" d="M395 717 V970 A167.5 167.5 0 0 0 730 970 V520 A168.5 168.5 0 0 1 1067 520 V970 A168.5 168.5 0 0 0 1404 970 V520 A168 168 0 0 1 1740 520 V970 A168 168 0 0 0 2076 970 V717"/>
    <path class="road-fill" d="M395 717 V970 A167.5 167.5 0 0 0 730 970 V520 A168.5 168.5 0 0 1 1067 520 V970 A168.5 168.5 0 0 0 1404 970 V520 A168 168 0 0 1 1740 520 V970 A168 168 0 0 0 2076 970 V717"/>
    <rect x="270" y="712" width="250" height="8" fill="var(--road)"/>
    <rect x="1951" y="712" width="250" height="8" fill="var(--road)"/>
    <path d="M270 717 H520 M1951 717 H2201" stroke="var(--road-edge)" stroke-width="3"/>
    <path class="road-centre" d="M395 760 V970 A167.5 167.5 0 0 0 730 970 V520 A168.5 168.5 0 0 1 1067 520 V970 A168.5 168.5 0 0 0 1404 970 V520 A168 168 0 0 1 1740 520 V970 A168 168 0 0 0 2076 970 V730"/>
  </g>

  <g class="label-masks">
    <rect class="label-mask" x="290" y="800" width="215" height="100"/>
    <rect class="label-mask" x="445" y="1085" width="240" height="100"/>
    <rect class="label-mask" x="770" y="295" width="255" height="100"/>
    <rect class="label-mask" x="1010" y="580" width="100" height="320"/>
    <rect class="label-mask" x="1070" y="1085" width="330" height="100"/>
    <rect class="label-mask" x="1420" y="285" width="310" height="130"/>
    <rect class="label-mask" x="1685" y="570" width="100" height="350"/>
    <rect class="label-mask" x="1780" y="1085" width="280" height="100"/>
  </g>

  <g class="labels">
    <text class="step-label" x="397" y="843">PARENT</text>
    <text class="step-label" x="397" y="886">INFORMATION</text>
    <text class="step-label" x="563" y="1125">STUDENT</text>
    <text class="step-label" x="563" y="1168">INFORMATION</text>
    <text class="step-label" x="897" y="340">APPROVING</text>
    <text class="step-label" x="897" y="382">EXCURSION</text>
    <g transform="translate(1070 743) rotate(90)">
      <text class="step-label" x="0" y="-2">THE SCHOOL ACCEPTS</text>
      <text class="step-label" x="0" y="41">ALL THE UPDATE</text>
    </g>
    <text class="step-label" x="1235" y="1125">THE SCHOOL MANAGES</text>
    <text class="step-label" x="1235" y="1168">THE EXCURSION</text>
    <text class="step-label" x="1571" y="326">THE SCHOOL TAKES</text>
    <text class="step-label" x="1571" y="363">THE CHILDREN TO THE</text>
    <text class="step-label" x="1567" y="405">EXCURSION</text>
    <g transform="translate(1743 743) rotate(90)">
      <text class="step-label" x="0" y="-2">THE SCHOOL CONDUCTS</text>
      <text class="step-label" x="0" y="41">ACTIVITY</text>
    </g>
    <text class="step-label" x="1920" y="1125">STUDENTS RETURN</text>
    <text class="step-label" x="1920" y="1168">TO SCHOOL</text>
  </g>

  <g class="pins">
    <a class="step-link" href="#parents">
      <path d="M342 665 L395 745 L448 665 Z" fill="var(--parent)"/>
      <circle class="pin-disc" cx="395" cy="620" r="70" stroke="var(--parent)"/>
      <rect role="img" aria-label="Icon: two parents" x="352" y="580" width="86" height="76" rx="14" fill="url(#icon-parent)"/>
    </a>
    <a class="step-link" href="#students">
      <path d="M505 1283 L558 1203 L611 1283 Z" fill="var(--student)"/>
      <circle class="pin-disc" cx="558" cy="1327" r="70" stroke="var(--student)"/>
      <rect role="img" aria-label="Icon: student" x="526" y="1282" width="64" height="86" rx="14" fill="url(#icon-student)"/>
    </a>
    <a class="step-link" href="#approvals">
      <path d="M845 210 L898 288 L951 210 Z" fill="var(--approve)"/>
      <circle class="pin-disc" cx="898" cy="165" r="70" stroke="var(--approve)"/>
      <rect role="img" aria-label="Icon: route map with pin" x="860" y="124" width="78" height="76" rx="12" fill="url(#icon-approve)"/>
    </a>
    <a class="step-link" href="#school-updates">
      <path d="M925 690 L1005 743 L925 796 Z" fill="var(--accept)"/>
      <circle class="pin-disc" cx="882" cy="743" r="70" stroke="var(--accept)"/>
      <rect role="img" aria-label="Icon: computer screen with update arrows" x="842" y="708" width="80" height="74" rx="10" fill="url(#icon-accept)"/>
    </a>
    <a class="step-link" href="#excursion-management">
      <path d="M1184 1283 L1237 1203 L1290 1283 Z" fill="var(--manage)"/>
      <circle class="pin-disc" cx="1237" cy="1327" r="70" stroke="var(--manage)"/>
      <rect role="img" aria-label="Icon: driver with vehicle and location pin" x="1204" y="1288" width="72" height="72" rx="12" fill="url(#icon-manage)"/>
    </a>
    <a class="step-link" href="#transport">
      <path d="M1519 210 L1572 288 L1625 210 Z" fill="var(--take)"/>
      <circle class="pin-disc" cx="1572" cy="165" r="70" stroke="var(--take)"/>
      <rect role="img" aria-label="Icon: teacher leading a group" x="1530" y="120" width="84" height="84" rx="12" fill="url(#icon-take)"/>
    </a>
    <a class="step-link" href="#activities">
      <path d="M1600 690 L1682 743 L1600 796 Z" fill="var(--conduct)"/>
      <circle class="pin-disc" cx="1558" cy="743" r="70" stroke="var(--conduct)"/>
      <rect role="img" aria-label="Icon: hiker reaching an achievement badge" x="1514" y="702" width="84" height="82" rx="12" fill="url(#icon-conduct)"/>
    </a>
    <a class="step-link" href="#safe-return">
      <path d="M1867 1283 L1920 1203 L1973 1283 Z" fill="var(--return)"/>
      <circle class="pin-disc" cx="1920" cy="1327" r="70" stroke="var(--return)"/>
      <rect role="img" aria-label="Icon: school building" x="1882" y="1286" width="78" height="70" rx="10" fill="url(#icon-return)"/>
    </a>
  </g>
</svg>
</body>
</html>
```